Business card por a urban DJ, up scale audience target

Need a sober design, modern, conservative colors but i can consider some options, y play rnb, hip hop, EDM and top40.

Business card for contact and personal info, double sided, use logo attrached please; im 42 so i need a card acording to my age an target audience.

Target Market(s)

Adult people, up scale audience

Industry/Entity Type

Music Download

Contact Information for Business Card

Cel (318) 4207265518 www.lumadrift.com

Requirements
Must have
• open mind
Nice to have
• open mind
Should not have
• DJ

```html
<!DOCTYPE html>
<html lang="en">
<head>
<meta charset="utf-8">
<title>LUMA – Business Card, Both Sides</title>
<link href="https://fonts.googleapis.com/css2?family=Arimo:wght@400;700&display=swap" rel="stylesheet">
<style>
  :root {
    --stage: #d9d6d1;
    --card: #f7f7f7;
    --ink: #1c1c1c;
    --mark: #333333;
    --muted: #3a3a3a;
    --band: #050505;
    --swoosh: #9a9a9a;
    --address: #ffffff;
    --back: #050505;
    --back-block: #f7f7f7;
  }
  * { margin: 0; padding: 0; box-sizing: border-box; }
  html, body { width: 1200px; height: 902px; overflow: hidden; background: var(--stage); }
  body { position: relative; font-family: "Arimo", Arial, sans-serif; }

  .card {
    position: absolute; left: 240px;
    width: 720px; height: 412px;
    overflow: hidden;
    box-shadow: 0 10px 24px rgba(0,0,0,.25);
  }
  .card-back { top: 26px; background: var(--back); }
  .card-front { top: 464px; background: var(--card); }

  /* back side */
  .back-block {
    position: absolute; left: 190px; top: 131px;
    width: 340px; height: 150px;
    background: var(--back-block);
    display: flex; align-items: center; justify-content: center;
  }
  .back-brand {
    display: flex; align-items: center; gap: 12px;
    color: var(--band);
    font-weight: 700; font-size: 76px; letter-spacing: 1px; line-height: 1;
  }
  .back-brand .brand-square { background: var(--band); }

  /* front side */
  .card-curves { position: absolute; inset: 0; width: 100%; height: 100%; }

  .brand {
    position: absolute; left: 62px; top: 134px;
    display: flex; align-items: center; gap: 12px;
    color: var(--mark);
    font-weight: 700; font-size: 76px; letter-spacing: 1px; line-height: 1;
  }
  .brand-square { width: 23px; height: 23px; background: var(--mark); flex: none; }

  .divider {
    position: absolute; left: 374px; top: 41px;
    width: 2px; height: 206px; background: var(--ink);
  }

  .person { position: absolute; left: 401px; top: 46px; color: var(--ink); }
  .person-name { font-weight: 700; font-size: 26px; line-height: 1.1; }
  .person-role { font-size: 18px; color: var(--muted); margin-top: 4px; }

  .contacts {
    position: absolute; left: 401px; top: 136px;
    list-style: none; color: var(--ink); font-size: 15px;
  }
  .contacts li { display: flex; align-items: center; gap: 10px; height: 25px; }
  .contacts svg { width: 13px; height: 13px; flex: none; }

  .address {
    position: absolute; left: 240px; bottom: 22px;
    color: var(--address); font-size: 16px; letter-spacing: .4px;
    white-space: nowrap;
  }
</style>
</head>
<body>
  <section class="card card-back" aria-label="Card back">
    <div class="back-block">
      <div class="back-brand"><span class="brand-square"></span>LUMA</div>
    </div>
  </section>

  <section class="card card-front" aria-label="Card front">
    <svg class="card-curves" viewBox="0 0 1050 600" preserveAspectRatio="none" aria-hidden="true">
      <path d="M0,540 C320,520 700,400 1050,270 L1050,300 C700,430 320,540 0,560 Z" fill="var(--swoosh)"/>
      <path d="M0,600 L0,575 C320,555 700,440 1050,305 L1050,600 Z" fill="var(--band)"/>
    </svg>

    <div class="brand"><span class="brand-square"></span>LUMA</div>

    <div class="divider"></div>

    <div class="person">
      <p class="person-name">Marcus Ellery</p>
      <p class="person-role">Managing Director</p>
    </div>

    <ul class="contacts">
      <li>
        <svg viewBox="0 0 18 18"><rect width="18" height="18" rx="2" fill="var(--ink)"/><path d="M5 4h3l1 3-2 1a7 7 0 0 0 3 3l1-2 3 1v3a1 1 0 0 1-1 1A10 10 0 0 1 4 5a1 1 0 0 1 1-1z" fill="#fff"/></svg>
        (318) 4207265518
      </li>
      <li>
        <svg viewBox="0 0 18 18"><rect width="18" height="18" rx="2" fill="var(--ink)"/><circle cx="9" cy="9" r="5" fill="none" stroke="#fff" stroke-width="1.5"/><path d="M4 9h10M9 4c-2 3-2 7 0 10M9 4c2 3 2 7 0 10" stroke="#fff" stroke-width="1" fill="none"/></svg>
        www.lumadrift.com
      </li>
      <li>
        <svg viewBox="0 0 18 18"><rect width="18" height="18" rx="2" fill="var(--ink)"/><rect x="3.5" y="5.5" width="11" height="7" fill="none" stroke="#fff" stroke-width="1.3"/><path d="M3.5 5.5 9 10l5.5-4.5" fill="none" stroke="#fff" stroke-width="1.3"/></svg>
        info@lumadrift.com
      </li>
    </ul>

    <p class="address">248 Harlow St, Suite Brookfield MA 0462</p>
  </section>
</body>
</html>
```